BOLD & MINIMALIST DESIGN NEEDED

We want a very bold but minimalistic business card design that is impactful and utilizes both sides of the business card. Our current logo is included for your use.

We want bold fonts and good use of negative space. We don't want the logo to overpower the design.

Target Market(s)

Professionals who are building new commercial buildings.

Industry/Entity Type

Construction

Contact Information for Business Card

Name, Title, email, office phone, cell phone, website

Font styles to use
Serif
Sans Serif

Requirements
Must have
• Bold design!

```html
<!DOCTYPE html>
<html lang="en">
<head>
<meta charset="utf-8">
<title>Ridgeline Design + Build — Business Card</title>
<link href="https://fonts.googleapis.com/css2?family=Arimo:wght@400;700&display=swap" rel="stylesheet">
<style>
  :root {
    --canvas: #e6e6e6;
    --card-white: #ffffff;
    --ink: #141414;
    --ink-soft: #555555;
    --green: #8cc63f;
    --green-deep: #7dbb2b;
    --green-light: #b4dc78;
    --green-wash: #c9e89c;
  }
  * { box-sizing: border-box; margin: 0; padding: 0; }
  html, body {
    width: 1200px;
    height: 1200px;
    overflow: hidden;
    background: var(--canvas);
    font-family: "Arimo", Arial, sans-serif;
  }
  .sheet {
    position: relative;
    width: 1200px;
    height: 1200px;
  }
  .card {
    position: absolute;
    left: 256px;
    width: 688px;
    height: 394px;
    overflow: hidden;
  }
  .card--front {
    top: 158px;
    background: var(--card-white);
  }
  .card--back {
    top: 652px;
    background: radial-gradient(ellipse at 50% 45%, var(--green-wash) 0%, var(--green) 60%, var(--green-deep) 100%);
  }

  /* Front: brand */
  .brand {
    position: absolute;
    left: 48px;
    top: 128px;
    display: flex;
    align-items: center;
    gap: 12px;
  }
  .brand__square {
    width: 26px;
    height: 26px;
    background: var(--green);
  }
  .brand__name {
    font-weight: 700;
    font-size: 34px;
    letter-spacing: 0.5px;
    color: var(--ink);
  }

  /* Front: person */
  .accent-bar {
    position: absolute;
    left: 0;
    top: 300px;
    width: 14px;
    height: 50px;
    background: linear-gradient(90deg, var(--green-deep), var(--green-light));
  }
  .person {
    position: absolute;
    left: 48px;
    top: 305px;
  }
  .person__name {
    font-weight: 700;
    font-size: 26px;
    color: var(--ink);
    letter-spacing: 0.3px;
  }
  .person__title {
    font-size: 15px;
    color: var(--green);
    margin-top: 2px;
  }

  /* Front: contact */
  .contact {
    position: absolute;
    top: 311px;
    list-style: none;
    font-size: 16px;
    color: var(--ink-soft);
    line-height: 20px;
  }
  .contact--phones { left: 282px; }
  .contact--web { left: 460px; }
  .contact li {
    display: flex;
    align-items: center;
    gap: 8px;
  }
  .contact svg { width: 13px; height: 13px; fill: var(--ink); flex: none; }

  /* Back */
  .back-brand {
    position: absolute;
    inset: 0;
    display: flex;
    align-items: center;
    justify-content: center;
    font-weight: 700;
    font-size: 62px;
    letter-spacing: 1px;
    color: var(--green-light);
  }
</style>
</head>
<body>
<main class="sheet">

  <section class="card card--front" aria-label="Card front">
    <div class="brand">
      <span class="brand__square"></span>
      <span class="brand__name">RIDGELINE</span>
    </div>

    <span class="accent-bar"></span>
    <div class="person">
      <p class="person__name">DANIEL REYES</p>
      <p class="person__title">President</p>
    </div>

    <ul class="contact contact--phones">
      <li>
        <svg viewBox="0 0 16 16" aria-hidden="true"><path d="M3.6 1.2l2.2 2.6-1.3 1.7c.9 2 2.4 3.5 4.3 4.4l1.7-1.3 2.6 2.2-1.2 2.6C6.5 13.2 2.8 9.5 1 3.6z"/></svg>
        555-210-4187
      </li>
      <li>
        <svg viewBox="0 0 16 16" aria-hidden="true"><path d="M4 0h8v16H4zM5.5 2v11h5V2z"/></svg>
        555-310-7724
      </li>
    </ul>

    <ul class="contact contact--web">
      <li>
        <svg viewBox="0 0 16 16" aria-hidden="true"><path d="M1 3h14v10H1zM2.5 4.5v.4L8 9l5.5-4.1v-.4z"/></svg>
        info@ridgelinebuild.com
      </li>
      <li>
        <svg viewBox="0 0 16 16" aria-hidden="true"><path d="M8 1a7 7 0 100 14A7 7 0 008 1zm-1 2.5l2 1-1 2 2 1.5-1 3-2-1V7L5 5.5z"/></svg>
        www.ridgelinebuild.com
      </li>
    </ul>
  </section>

  <section class="card card--back" aria-label="Card back">
    <p class="back-brand">RIDGELINE</p>
  </section>

</main>
</body>
</html>
```